Flyer für eine Tagespflege (Senioren & Demenzkranke)
Zielgruppe
Hallo wir sind eine Tagespflege die 365 Tage im Jahr geöffnet hat. Wir kümmern uns um Senioren und Demenzkranke. Zielgruppe sind Personen die Ihre Angehörigen (zur Entlastung) Zuhause pflegen und Senioren die den Tag in Gemeinschaft verbringen wollen und abends zu Hause im eigenen Bett schlafen wollen
Aufgabenstellung
Es sollte ansprechend bzw. hochwertig aussehen. Es sollte ein Standard Format sein. Bei der Größe gibt es keine Vorgabe. Es sollte übersichtlich sein. Die Adresse sollte mit Karte dargestellt sein. Das wir 365 Tage im Jahr geöffnet haben muss klar hervor gehen.

```html
<!DOCTYPE html>
<html lang="de">
<head>
<meta charset="utf-8">
<title>Tagespflege Flyer</title>
<link href="https://fonts.googleapis.com/css2?family=Open+Sans:wght@300;400;600;700&family=Barlow+Condensed:wght@700&family=Fredoka:wght@600&display=swap" rel="stylesheet">
<style>
:root{
  --green:#2e8a30;
  --green-dark:#21762a;
  --mint:#f3f8f1;
  --text:#3a3a3a;
  --grey:#4a4a4a;
  --gold:#d9b84a;
}
*{margin:0;padding:0;box-sizing:border-box}
html,body{width:1200px;height:2400px;overflow:hidden;background:#fff}
body{position:relative;font-family:"Open Sans",sans-serif;color:var(--text)}
.abs{position:absolute}
.mint{background:var(--mint)}
.photo{position:absolute}
.h-section{font-family:"Open Sans",sans-serif;font-weight:300;color:var(--green);font-size:28px;letter-spacing:.3px;line-height:1}
.h-section b{font-weight:700}
.body-text{font-size:13.6px;line-height:21.7px;text-align:justify;font-weight:400}
.checklist{list-style:none;font-size:13.6px}
.checklist li{position:relative;padding-left:25px}
.checklist li::before{content:"√";position:absolute;left:0;color:var(--green);font-weight:600}

/* front */
.team-title{font-family:"Fredoka",sans-serif;color:var(--green);font-size:36px;line-height:43px;letter-spacing:1px}
.team-sub{font-weight:300;color:var(--green);font-size:28px;line-height:36px}
.person-name{font-weight:700;color:var(--green);font-size:24px;line-height:30px}
.person-role{font-size:13.6px;line-height:22px;color:var(--grey)}
.label{font-weight:700;color:var(--green);font-size:13px;margin-bottom:4px}
.contact-text{font-size:13.6px;line-height:22px}
.visit{text-align:center;font-weight:300;color:var(--green);font-size:22px;line-height:30px}
.visit b{font-weight:700}
.phone{border:5px solid #e4e4e4;border-bottom:none;border-radius:30px 30px 0 0;background:#f7f7f7;overflow:hidden}
.cover-frame{border:2px solid var(--green)}
.brand{font-family:"Barlow Condensed",sans-serif;font-weight:700;color:var(--green);font-size:54px;text-align:center;line-height:1}
.brand-sub{font-size:19px;color:var(--green);text-align:center;letter-spacing:.5px}

/* back */
.hero-text{font-weight:300;font-size:28px;line-height:37px;color:var(--grey)}
.hero-text b{display:block;font-weight:700;font-size:44px;line-height:52px;color:#3d3d3d}
.card{background:#fff;border-radius:28px 28px 0 0;padding:8px 8px 0}
.card-img{border-radius:22px 22px 0 0;height:184px}
.feature{font-weight:600;color:var(--green);font-size:14px;text-align:center}
.quote-title{font-weight:700;color:var(--green);font-size:28px;line-height:33px}
.quote-text{font-size:13.6px;line-height:25.5px}
.services li{line-height:20.5px;margin-bottom:4.5px}
</style>
</head>
<body>

<!-- ===== Front side ===== -->
<section class="front">
  <div class="abs mint" style="left:49px;top:338px;width:161px;height:352px"></div>
  <div class="abs mint" style="left:210px;top:690px;width:160px;height:450px"></div>

  <div class="abs" style="left:61px;top:390px;width:300px">
    <h2 class="h-section">UNSER <b>ANGEBOT</b></h2>
    <p class="body-text" style="margin-top:11px">Sie fühlen sich in Ihrem Zuhause wohl möchten oder können dort aber nicht den gesamten Tag über alleine sein? Unsere Tagespflege bietet Ihnen behaglich eingerichtete Räumlichkeiten, nette Gesellschaft und Abwechslung. Als Tagesgast in unserer 2017 eröffneten Einrichtung erwartet Sie hier täglich wechselnde sinnvolle Betreuungsangebote mit verschiedenen Aktivitäten, die auf jeden Tagesgast individuell abgestimmt sind. Das abwechslungsreiche Freizeitprogramm können Sie nach Ihren Wünschen wahrnehmen oder sich zwischendurch zurückziehen und Abgeschiedenheit und Ruhe genießen.</p>
    <p class="body-text" style="margin-top:4px;text-align:left">Unsere Tagespflege ist als einzige in Wiesenfeld an 365 Tagen im Jahr geöffnet!</p>
  </div>

  <svg class="abs" style="left:286px;top:781px" width="50" height="52" viewBox="0 0 50 52" fill="none" stroke="#444" stroke-width="1.6" aria-hidden="true">
    <path d="M3 24 L25 3 L47 24 M9 19 V49 H41 V19"/>
    <path d="M25 40 C14 32 17 23 22 25 C24 26 25 28 25 28 C25 28 26 26 28 25 C33 23 36 32 25 40Z"/>
  </svg>
  <svg class="abs" style="left:68px;top:843px" width="50" height="50" viewBox="0 0 50 50" fill="none" stroke="#444" stroke-width="1.6" aria-hidden="true">
    <path d="M25 38 C10 28 13 16 20 18 C23 19 25 22 25 22 C25 22 27 19 30 18 C37 16 40 28 25 38Z"/>
    <path d="M6 14 V34 L14 46 M44 14 V34 L36 46"/>
  </svg>
  <div class="abs" style="left:130px;top:800px">
    <div class="team-title">UNSER<br>PFLEGETEAM</div>
    <div class="team-sub">TRÄGT SIE<br>AUF HÄNDEN</div>
  </div>
  <div class="abs" style="left:61px;top:955px;width:300px">
    <ul class="checklist" style="line-height:24px">
      <li>12 erfahene Tagespfleger</li>
      <li>Hochmotiviert &amp; Ambitioniert</li>
      <li>Abwechslung und Spaß garantiert!</li>
    </ul>
    <p style="font-size:13.6px;line-height:25px">individuellen Wünsche und Fähigkeiten stehen an erster Stelle.</p>
  </div>

  <div class="photo" role="img" aria-label="Foto: Pflegedienstleitung am Schreibtisch mit Computer" style="left:428px;top:391px;width:149px;height:162px;border-radius:0 22px 0 0;background:linear-gradient(135deg,#eef0ee,#d7dbd6 55%,#5e6f52)"></div>
  <div class="abs" style="left:590px;top:425px">
    <div class="person-name">HELENA<br>VOGT</div>
    <div class="person-role" style="margin-top:2px">Pflegedienstleitung<br>&amp; Koordination</div>
  </div>
  <div class="abs" style="left:428px;top:588px">
    <div class="label">ADRESSE</div>
    <div class="contact-text">Birkenweg 14<br>17329 Wiesenfeld</div>
  </div>
  <div class="abs" style="left:564px;top:588px">
    <div class="label">KONTAKT</div>
    <div class="contact-text">Tel.Nr.:03981/4407125<br>tagespflege-mo@beispielpost.de</div>
  </div>

  <div class="abs mint" style="left:428px;top:694px;width:313px;height:290px"></div>
  <div class="abs visit" style="left:428px;top:708px;width:313px">BESUCHEN SIE UNS IM<br>BIRKENWEG 14<br><b>17329 WIESENFELD</b></div>
  <div class="abs phone" style="left:486px;top:818px;width:204px;height:322px">
    <div style="height:8px"></div>
    <div style="margin:30px 8px 0;height:34px;background:#fff;border-bottom:2px solid var(--green)"></div>
    <div role="img" aria-label="Stadtplan mit Markierung des Standorts der Tagespflege" style="margin:0 8px;height:240px;background:linear-gradient(160deg,#e6ebe3,#dfe6dc 60%,#c9dcc4)"></div>
  </div>

  <div class="abs mint" style="left:776px;top:338px;width:382px;height:267px"></div>
  <div class="photo" role="img" aria-label="Foto: heller Aufenthaltsraum mit Gästen am Tisch und Küchenzeile mit Obst" style="left:776px;top:605px;width:382px;height:535px;background:linear-gradient(180deg,#f4e9d6 0%,#f0d3a8 45%,#d9b28a 70%,#6b5a48 100%)"></div>
  <div class="abs cover-frame" style="left:795px;top:356px;width:345px;height:765px"></div>
  <svg class="abs" style="left:912px;top:387px" width="122" height="122" viewBox="0 0 122 122" aria-hidden="true"><circle cx="61" cy="61" r="58" fill="none" stroke="var(--green)" stroke-width="2"/></svg>
  <div class="abs" style="left:795px;top:524px;width:345px">
    <div class="brand">TAGESPFLEGE</div>
    <div class="brand-sub" style="margin-top:8px">Marlene Osterkamp</div>
  </div>
</section>

<!-- ===== Back side ===== -->
<section class="back">
  <div class="photo" role="img" aria-label="Foto: Obstkorb und Blumen im hellen Gemeinschaftsraum" style="left:49px;top:1224px;width:773px;height:326px;background:linear-gradient(120deg,#dde5e6 0%,#eef0ec 35%,#e9c66a 55%,#d98a3c 70%,#eef1ee 100%)"></div>
  <div class="abs mint" style="left:49px;top:1550px;width:249px;height:486px"></div>
  <div class="abs hero-text" style="left:89px;top:1271px">REICHHALTIGES<br>ANGEBOT:<br>FÜR IHR WOHL<b>&amp;FREUDE</b></div>

  <div class="abs card" style="left:80px;top:1451px;width:226px">
    <div class="card-img" role="img" aria-label="Foto: Hand greift zu einem Teller mit frischem Obst" style="background:linear-gradient(135deg,#f2e6cf,#f4d77a 50%,#e9a26c)"></div>
  </div>
  <div class="abs card" style="left:342px;top:1451px;width:226px">
    <div class="card-img" role="img" aria-label="Foto: Hand setzt eine Spielfigur auf einem Brettspiel" style="background:linear-gradient(135deg,#f1ece2,#e8d4a6 50%,#c7a56c)"></div>
  </div>
  <div class="abs card" style="left:603px;top:1451px;width:226px">
    <div class="card-img" role="img" aria-label="Foto: Küchenzeile mit Obstkorb im Gemeinschaftsraum" style="background:linear-gradient(160deg,#f2e7d4,#e7c089 55%,#3a3a3a)"></div>
  </div>

  <svg class="abs" style="left:176px;top:1647px" width="26" height="22" viewBox="0 0 26 22" fill="none" stroke="var(--gold)" stroke-width="1.6" aria-hidden="true"><path d="M13 20 C2 12 1 4 7 2 C10 1 12 3 13 5 C14 3 16 1 19 2 C25 4 24 12 13 20Z"/></svg>
  <svg class="abs" style="left:441px;top:1647px" width="26" height="22" viewBox="0 0 26 22" fill="none" stroke="var(--gold)" stroke-width="1.6" aria-hidden="true"><path d="M13 20 C2 12 1 4 7 2 C10 1 12 3 13 5 C14 3 16 1 19 2 C25 4 24 12 13 20Z"/></svg>
  <svg class="abs" style="left:701px;top:1647px" width="26" height="22" viewBox="0 0 26 22" fill="none" stroke="var(--gold)" stroke-width="1.6" aria-hidden="true"><path d="M13 20 C2 12 1 4 7 2 C10 1 12 3 13 5 C14 3 16 1 19 2 C25 4 24 12 13 20Z"/></svg>
  <div class="abs feature" style="left:80px;top:1671px;width:226px">Gesunde Ernährung</div>
  <div class="abs feature" style="left:342px;top:1671px;width:226px">Tolle Freizeitprogramme</div>
  <div class="abs feature" style="left:603px;top:1671px;width:226px">Gemeinsames kochen</div>

  <div class="abs" style="left:89px;top:1730px;width:320px">
    <h3 class="quote-title">GLÜCKLICH IST DER MENSCH, DER SEINEN NÄCHSTEN TRÄGT…</h3>
    <p class="quote-text" style="margin-top:10px">in seiner ganzen Gebrechlichkeit wie er sich<br>wünscht, von jenen getragen zu werden<br>in seiner ganzen Schwäche<br>(Anselm von Hohenfeld)</p>
  </div>

  <div class="abs" style="left:470px;top:1700px;width:318px">
    <h2 class="h-section">UNSERE <b>LEISTUNGEN…</b></h2>
    <ul class="checklist services" style="margin-top:9px">
      <li>365 Tage im Jahr täglich von 8.00 bis 16.00 Uhr geöffnet</li>
      <li>Kostenloser Schnuppertag</li>
      <li style="text-align:justify">Die Tagespflege können Sie für einen oder mehrere Tage sowie die ganze Woche in Anspruch nehmen.</li>
      <li>Mehrere Mahlzeiten wie Frühstück, Mittagessen und Kaffee</li>
      <li>Behandlungspflege (Medikamentengabe, Wundverbände, Injektionen usw.)</li>
      <li>Pflegerische Betreuung (Hilfe beim Toilettengang, Hilfe bei Nahrungsaufnahme usw.)</li>
    </ul>
  </div>

  <div class="abs" style="left:855px;top:1303px;width:303px">
    <h2 class="h-section">WAS WIR <b>BIETEN</b></h2>
    <p class="body-text" style="margin-top:11px">Mit unserer Tagespflege schließen wir die Lücke zwischen Häuslichkeit und Pflegeheim. Wir unterstützen unsere Gäste dabei, im Rahmen ihrer individuellen Fähigkeiten und Wünsche selbstbestimmt am Leben teilzunehmen und aktiv zu sein. Ihre Angehörigen werden gleichzeitig entlastet und können in Ruhe arbeiten. Besuchen Sie unser Gästehaus und schauen Sie sich um. Im persönlichen Gespräch beraten wir Sie vor Ort zu unseren Leistungen. Auf Wunsch vereinbaren Sie einen Termin. Gern können Sie dann, für ihren Angehörigen einen kostenlosen Schnuppertag in unserer Tagesspflege festlegen.</p>
  </div>
  <div class="photo" role="img" aria-label="Foto: Pflegerin und älterer Herr lachen gemeinsam im Garten" style="left:857px;top:1680px;width:302px;height:356px;border-radius:30px 0 0 0;background:linear-gradient(135deg,#7fa55a 0%,#b9cf8f 40%,#4f6b3a 70%,#8a6a4e 100%)"></div>
</section>

</body>
</html>
```